Tech Savy small Business accountant business card design

We need a business card for a new company based in the cloud. We provide tax, business advisory, accounting, information technology solutions and back office functions to small businesses. We offer fixed fee packages with add on services as you need them. By harnessing technology we simplify small business operational processes providing valuable time and information for small business owners to grow their business. In the logo (bluvoria) we want to be able to see bluv and experts. The final design should communicate achieving growth dreams and balance (ie life and $).
Updates
This project has been temporarily placed on hold until I finalize "Tech Savy small Business accountant needs a logo". I invite all designers to submit on this logo project. Once my logo is finalized I will resume this business card contest. Thanks Added Wednesday, March 19, 2014
This project has been temporarily placed on hold until I finalize "Tech Savy small Business accountant logo". I invite all designers to submit on this logo project. Once my logo is finalized I will resume this business card contest. Thanks Added Thursday, March 20, 2014
Target Market(s)
Small Business (Revenue $500,000, more than 3 employees) owners.
Industry/Entity Type
Small Business
Contact Information for Business Card
Marcy Elwind (Principal)
Accountant, Tax Agent.
TEL | 0417 683 912
EMAIL | Marcy.Elwind@bluvoria.com.au
WEB | www.bluvoria.com.au
Look and feel

```html
<!DOCTYPE html>
<html lang="en">
<head>
<meta charset="utf-8">
<title>bluvoria business card</title>
<link rel="stylesheet" href="https://fonts.googleapis.com/css2?family=Open+Sans:wght@400;600;700&display=swap">
<style>
  :root {
    --page: #e9e7e4;
    --card-black: #0c0c0d;
    --card-blue-light: #3fa9e4;
    --card-blue-deep: #1a6fc0;
    --divider: #ffffff;
    --ink-light: #ffffff;
    --ink-dark: #141414;
    --ink-title: #0d2236;
    --card-white: #ffffff;
  }
  * { margin: 0; padding: 0; box-sizing: border-box; }
  html, body {
    width: 1200px; height: 913px; overflow: hidden;
    background: var(--page);
    font-family: "Open Sans", Arial, sans-serif;
  }
  .sheet { position: relative; width: 1200px; height: 913px; }
  .card {
    position: absolute; top: 306px;
    width: 525px; height: 300px;
    border-radius: 16px; overflow: hidden;
    box-shadow: 0 6px 18px rgba(0,0,0,.18);
  }
  .card--front { left: 60px; }
  .card--back { left: 615px; background: var(--card-white); }
  .card__bg { position: absolute; inset: 0; }
  .wordmark {
    position: absolute; font-weight: 700; letter-spacing: -1px; line-height: 1;
  }
  .tagline { position: absolute; font-weight: 400; white-space: nowrap; line-height: 1.3; }
  .card--front .wordmark { left: 38px; top: 38px; font-size: 56px; color: var(--ink-light); }
  .card--front .tagline { left: 42px; top: 100px; font-size: 15px; color: var(--ink-light); }
  .holder { position: absolute; left: 38px; top: 232px; color: var(--ink-light); }
  .holder__name { font-size: 15px; font-weight: 700; letter-spacing: .3px; }
  .holder__role { font-size: 13px; color: var(--ink-title); margin-left: 70px; margin-top: 2px; }
  .contacts {
    position: absolute; left: 300px; top: 168px; list-style: none;
    font-size: 12.5px; color: var(--ink-light);
  }
  .contacts li { display: flex; align-items: center; gap: 8px; height: 21px; }
  .contacts svg { width: 12px; height: 12px; fill: var(--ink-light); flex: none; }
  .card--back .wordmark { left: 0; right: 0; top: 104px; text-align: center; font-size: 64px; color: var(--ink-dark); }
  .card--back .tagline { left: 0; right: 0; top: 178px; text-align: center; font-size: 17px; font-weight: 600; color: var(--ink-dark); }
</style>
</head>
<body>
<main class="sheet">
  <section class="card card--front" aria-label="Card front">
    <svg class="card__bg" viewBox="0 0 525 300" preserveAspectRatio="none" aria-hidden="true">
      <defs>
        <linearGradient id="blueFill" x1="0" y1="0" x2="0" y2="1">
          <stop offset="0" stop-color="var(--card-blue-light)"/>
          <stop offset="1" stop-color="var(--card-blue-deep)"/>
        </linearGradient>
      </defs>
      <rect width="525" height="300" fill="url(#blueFill)"/>
      <path d="M0,0 H525 V70 C420,120 220,185 0,200 Z" fill="var(--card-black)"/>
      <path d="M0,200 C220,185 420,120 525,70" fill="none" stroke="var(--divider)" stroke-width="4"/>
    </svg>
    <div class="wordmark">bluvoria</div>
    <div class="tagline">Your business and accounting partner</div>
    <ul class="contacts">
      <li><svg viewBox="0 0 24 24"><path d="M6.6 10.8a15.1 15.1 0 0 0 6.6 6.6l2.2-2.2a1 1 0 0 1 1-.25 11.4 11.4 0 0 0 3.6.57 1 1 0 0 1 1 1V20a1 1 0 0 1-1 1A17 17 0 0 1 3 4a1 1 0 0 1 1-1h3.5a1 1 0 0 1 1 1c0 1.25.2 2.45.57 3.57a1 1 0 0 1-.25 1z"/></svg>0417 683 912</li>
      <li><svg viewBox="0 0 24 24"><path d="M12 2a10 10 0 1 0 0 20 10 10 0 0 0 0-20zm6.9 6h-3a15.6 15.6 0 0 0-1.4-3.6A8 8 0 0 1 18.9 8zM12 4c.8 1.2 1.5 2.5 1.9 4h-3.8c.4-1.4 1.1-2.8 1.9-4zM4.3 14a8 8 0 0 1 0-4h3.4a16 16 0 0 0 0 4zm.8 2h3a15.6 15.6 0 0 0 1.4 3.6A8 8 0 0 1 5.1 16zm3-8h-3a8 8 0 0 1 4.4-3.6C8.9 5.5 8.4 6.7 8.1 8zM12 20c-.8-1.2-1.5-2.5-1.9-4h3.8c-.4 1.4-1.1 2.8-1.9 4zm2.3-6H9.7a14.7 14.7 0 0 1 0-4h4.6a14.7 14.7 0 0 1 0 4zm.3 5.6c.6-1.1 1.1-2.3 1.4-3.6h3a8 8 0 0 1-4.4 3.6zm1.7-5.6a16 16 0 0 0 0-4h3.4a8 8 0 0 1 0 4z"/></svg>www.bluvoria.com.au</li>
      <li><svg viewBox="0 0 24 24"><path d="M2 5h20v14H2zm2 2v.5l8 5 8-5V7zm0 2.8V17h16V9.8l-8 5z"/></svg>Marcy.Elwind@bluvoria.com.au</li>
    </ul>
    <div class="holder">
      <div class="holder__name">MARCY ELWIND (Principal)</div>
      <div class="holder__role">Accountant, Tax Agent</div>
    </div>
  </section>

  <section class="card card--back" aria-label="Card back">
    <div class="wordmark">bluvoria</div>
    <div class="tagline">Your business and accounting partner</div>
  </section>
</main>
</body>
</html>
```